Business Card Design For A Cajun Seafood Restaurant

We are opening a cajun seafood restaurant in a week. We mainly serve cajun seafood which is orginally from Louisiana. We want design on both sides of a business card. I have menu on the website. You can go to www.reednkettle.example to check out our menu.

Restaurant name: Reed N' Kettle
Phone: +1 (555) 304-7712
Address: 48206 Ludlow Row, #7, Bexmoor Flats, Ca90000
Email: reednkettle@mailbox.example
Website: www.reednkettle.example

Maybe add social media icons (facebook, instagram) if looks nice on the business card.
facebook.com/reednkettle
instagram.com/reednkettle or @reednkettle

Attached is the logo and other business card samples that I like.

```html
<!DOCTYPE html>
<html lang="en">
<head>
<meta charset="utf-8">
<title>Reed N' Kettle — Business Card</title>
<link rel="stylesheet" href="https://fonts.googleapis.com/css2?family=Source+Sans+3:wght@400;700&display=swap">
<style>
  :root {
    --page: #e9e6e1;
    --orange: #ff6a00;
    --crab-light: #f28a3c;
    --crab-dark: #d8531a;
    --corn: #f4c430;
    --ink: #1b1b1b;
    --paper: #ffffff;
    --text: #2a2a2a;
  }
  * { box-sizing: border-box; margin: 0; padding: 0; }
  html, body { width: 1200px; height: 900px; overflow: hidden; }
  body {
    background: var(--page);
    font-family: "Source Sans 3", Arial, sans-serif;
    display: flex;
    flex-direction: column;
    align-items: center;
    justify-content: center;
    gap: 40px;
  }
  .card {
    width: 700px;
    height: 400px;
    position: relative;
    overflow: hidden;
    box-shadow: 0 4px 14px rgba(0,0,0,.18);
  }
  .card-front { background: var(--orange); }
  .card-back { background: var(--paper); }

  .mascot-art {
    position: absolute;
    background: radial-gradient(circle at 50% 40%, var(--corn) 0 18%, var(--crab-light) 19% 55%, var(--crab-dark) 100%);
    border-radius: 40% 40% 35% 35%;
  }
  .card-front .mascot-art { width: 190px; height: 160px; left: 255px; top: 58px; }
  .card-back .mascot-art { width: 320px; height: 260px; left: 40px; top: 160px; }

  .wordmark {
    display: flex;
    align-items: center;
    gap: 10px;
    font-weight: 700;
    color: var(--ink);
    letter-spacing: .02em;
    text-transform: uppercase;
  }
  .wordmark-dot { width: 14px; height: 14px; background: var(--corn); flex: none; }
  .tagline {
    font-weight: 700;
    text-transform: uppercase;
    letter-spacing: .06em;
    color: var(--ink);
  }
  .card-front .brand {
    position: absolute; left: 0; right: 0; top: 232px;
    display: flex; flex-direction: column; align-items: center; gap: 6px;
  }
  .card-front .wordmark { font-size: 44px; }
  .card-front .tagline { font-size: 20px; }

  .card-back .brand {
    position: absolute; right: 56px; top: 44px;
    display: flex; flex-direction: column; align-items: flex-end; gap: 2px;
  }
  .card-back .wordmark { font-size: 38px; }
  .card-back .tagline { font-size: 17px; }

  .contact-list {
    position: absolute; right: 56px; top: 150px;
    list-style: none;
    text-align: right;
    color: var(--text);
    font-size: 16px;
    line-height: 1.5;
  }
  .contact-list li { display: flex; justify-content: flex-end; align-items: center; gap: 8px; }
  .contact-icon { width: 12px; height: 12px; fill: var(--orange); flex: none; }
  .icon-spacer { width: 12px; flex: none; }
</style>
</head>
<body>
  <section class="card card-front">
    <div class="mascot-art" role="img" aria-label="Illustration of a cartoon crab holding an ear of corn"></div>
    <div class="brand">
      <div class="wordmark"><span class="wordmark-dot"></span>Reed N' Kettle</div>
      <div class="tagline">Cajun Seafood House</div>
    </div>
  </section>

  <section class="card card-back">
    <div class="brand">
      <div class="wordmark"><span class="wordmark-dot"></span>Reed N' Kettle</div>
      <div class="tagline">Cajun Seafood House</div>
    </div>
    <ul class="contact-list">
      <li>+1 (555) 304-7712
        <svg class="contact-icon" viewBox="0 0 12 12"><path d="M2 1h3l1 3-1.5 1a6 6 0 0 0 2.5 2.5L8 6l3 1v3a1 1 0 0 1-1 1A9 9 0 0 1 1 2a1 1 0 0 1 1-1z"/></svg></li>
      <li>reednkettle@mailbox.example
        <svg class="contact-icon" viewBox="0 0 12 12"><rect x="0" y="2" width="12" height="8" rx="1"/><path d="M0 3l6 4 6-4" stroke="#fff" fill="none"/></svg></li>
      <li>www.reednkettle.example
        <svg class="contact-icon" viewBox="0 0 12 12"><circle cx="6" cy="6" r="6"/><path d="M0 6h12M6 0v12" stroke="#fff"/></svg></li>
      <li>48206 Ludlow Row, #7,
        <svg class="contact-icon" viewBox="0 0 12 12"><path d="M6 0a4 4 0 0 1 4 4c0 3-4 8-4 8S2 7 2 4a4 4 0 0 1 4-4z"/><circle cx="6" cy="4" r="1.5" fill="#fff"/></svg></li>
      <li>Bexmoor Flats, Ca90000<span class="icon-spacer"></span></li>
      <li>www.facebook.com/reednkettle<span class="icon-spacer"></span></li>
      <li>www.instagram.com/reednkettle<span class="icon-spacer"></span></li>
    </ul>
    <div class="mascot-art" role="img" aria-label="Large illustration of a cartoon crab holding an ear of corn overhead"></div>
  </section>
</body>
</html>
```